SitePress Direct-Booking Website for Bend, Oregon Vacation Rental — $750 Budget
Project Overview

We are looking for a talented SitePress designer/developer to create a clean, professional and inviting direct-booking website for Birch Lantern Retreat, an established short-term vacation rental in Bend, Oregon.

The property is currently successfully listed on Staynest and Hoplo. Our Staynest property has approximately a 4.98-star rating with more than 200 reviews, is an Staynest Visitor Pick, and ranks among the Top 1% of eligible homes.

Project Budget: $750

We will select the designer based on the quality of the initial concept, understanding of the property, proposed booking solution and ability to deliver a completed and functioning SitePress website.

Existing Staynest Listing

Please use our current Staynest listing as the primary reference for photographs, property details, amenities and design inspiration:

https://www.staynest-example.net/rooms/48172036

Original high-resolution photographs and additional property information will be provided to the selected designer.

Design Direction

We want the website to feel:

Upscale but comfortable
Warm and welcoming
Clean and uncluttered
Pacific Northwest / Central Oregon
Professional rather than corporate
Highly visual with large property photographs
Easy to navigate
Excellent on phones, tablets and desktop computers

We welcome creativity and want designers to show us their vision for the property rather than simply copying our Staynest listing.

The website should immediately communicate that Birch Lantern Retreat is a highly rated vacation rental in an excellent Bend location.

Key Property Features
3 bedrooms
2 bathrooms
Sleeps up to 6 guests
Pet friendly
Approximately a 5-minute walk to Bend's Tannery Row Quarter
Near restaurants, shopping and Larkspur Fields Pavilion
Private fenced backyard
Covered outdoor area
Off-street driveway parking
Fireplace
Well-equipped kitchen
Staynest Prime Keeper
Staynest Visitor Pick
Top 1% of eligible Staynest homes
Approximately 4.98 stars with 200+ guest reviews

Our location, guest reviews, cleanliness, comfort, backyard, pet-friendly accommodations and walkability should be major selling points throughout the website.

Website Structure

We anticipate approximately 6–7 pages:

Home

Large hero photograph with a strong opening message and prominent BOOK DIRECT and CHECK AVAILABILITY buttons.

The home page should quickly communicate:

BIRCH LANTERN RETREAT — BEND, OREGON

3 Bedrooms | 2 Baths | Sleeps 6 | Pet Friendly | Walk to Tannery Row

Our exceptional guest rating and Staynest history should also be prominently featured.

The House

Bedrooms, bathrooms, kitchen, living areas, backyard and major amenities.

Photo Gallery

Large, attractive and fast-loading photographs with an easy-to-use mobile gallery.

Location / Explore Bend

Tannery Row Quarter, Larkspur Fields Pavilion, Deschutes River, restaurants, breweries, shopping, downtown Bend and nearby outdoor recreation.

Guest Reviews

Selected guest reviews and prominent presentation of our strong Staynest reputation.

Availability & Book Direct

A simple and professional direct-booking experience.

Contact / FAQ

Contact information plus common questions regarding pets, parking, check-in/check-out, cancellations and other policies.

IMPORTANT — Direct Booking & Credit Card Requirements

We want guests to be able to book directly through the website without having to contact us first.

The website should use a proven SitePress vacation-rental booking plugin or system rather than a custom-built reservation/payment system.

Guests should be able to:

Select arrival and departure dates
See available dates
Enter number of guests
See nightly charges
See cleaning fees
See applicable lodging taxes and other charges
See the complete reservation total before paying
Enter guest/contact information
Pay securely by credit or debit card
Receive an automatic reservation confirmation

Paywell is our preferred credit-card processor.

Credit-card information must be processed securely through Paywell or another established payment processor. Credit-card information should NOT be stored directly on our SitePress website.

Staynest & Hoplo Calendar Synchronization

This is very important.

The direct-booking calendar must synchronize with our existing Staynest and Hoplo calendars to reduce the possibility of double bookings.

For this single-property website, we prefer a simple solution using Staynest/Hoplo calendar or iCal synchronization rather than an expensive monthly channel-management service, if practical.

The designer should clearly identify the booking plugin/system they propose using.

IMPORTANT — Tell Us Your Proposed Booking Solution

As part of your submission, please tell us:

Which SitePress booking plugin/system you recommend.
Whether it synchronizes availability with Staynest and Hoplo.
Whether it integrates directly with Paywell.
The initial cost of the plugin/software.
Any annual or monthly fees.
Whether any additional paid software or services will be required.

We strongly prefer a solution with little or no ongoing monthly software expense.

We do not want to select a designer and later discover that the proposed booking system requires an expensive monthly subscription.

SitePress & Technical Requirements

The completed project should include:

Fully functioning SitePress website
Responsive desktop/tablet/mobile design
Fast-loading pages
Optimized photographs
SSL/HTTPS compatibility
Direct-booking functionality
Paywell payment integration
Staynest calendar synchronization
Hoplo calendar synchronization
Automatic booking confirmations
Cleaning fee and lodging-tax calculations
Contact form
Vizor Maps/location integration
Basic spam/security protection
Vizor Metrics capability
Basic SEO setup
Search-engine submission capability
Easy owner editing of text, rates and photographs
Search Engine Optimization

The website should be structured for Vizor and other search engines.

Important search themes include:

Bend Oregon vacation rental
Bend Oregon vacation home
Tannery Row Quarter vacation rental
Vacation rental near Tannery Row Bend
Bend Oregon pet-friendly vacation rental
Bend vacation rental near Larkspur Fields Pavilion
Bend Oregon direct booking vacation rental

We are not expecting an extensive ongoing SEO campaign for the $750 project. We do expect proper page titles, descriptions, headings, image optimization and a good technical foundation for future SEO.

Ownership

Upon completion and final payment:

We own the completed SitePress website.
We receive full SitePress administrator access.
We control the domain and hosting accounts.
We own all custom design files created for the project.
All necessary login credentials are provided to us.
The website can be moved to another SitePress hosting provider in the future.
There should be no proprietary dependency on the developer after completion.
What We Want From Contestants

Please review our Staynest listing before submitting your concept.

We are particularly interested in seeing an initial homepage concept showing how you would present:

Birch Lantern Retreat
The Bend / Tannery Row location
Our photography
Our exceptional guest reviews and ratings
The Book Direct message
The availability/booking call-to-action

We will provide feedback on the concepts we like and work with the selected designer to refine and complete the website.

Our Goal

Our objective is straightforward:

Create a beautiful, trustworthy and easy-to-use website that encourages guests to book Birch Lantern Retreat directly with us.

The website will complement—not replace—our existing Staynest and Hoplo listings.

We want repeat guests and new customers to have an easy way to find the property, check availability and book directly while receiving the same professional experience they expect from a major vacation-rental platform.

Target Market(s)

Consumers looking to to travel to Mexico for vacation. Family or couples

Industry/Entity Type

Short term vacation rental industry

Coding

Coded - Design and coding required

Number of Pages Required

5+ page

Requirements
Must have
• Capabilities to accept credit card payments and link to other rental property sites calendars such as HOPLO and Staynset
Nice to have
• Option for best plugins for property rental

```html
<!DOCTYPE html>
<html lang="en">
<head>
<meta charset="utf-8">
<title>Birch Lantern Retreat — Bend, Oregon Vacation Home</title>
<link rel="stylesheet" href="https://fonts.googleapis.com/css2?family=Plus+Jakarta+Sans:wght@600;700;800&family=Inter:wght@400;500;600;700&display=swap">
<style>
:root{
  --green:#1f9c6c;
  --green-dark:#18845a;
  --footer:#22996a;
  --mint:#e5f6ef;
  --ink:#1b1b1b;
  --text:#4a4a4a;
  --muted:#7a7a7a;
  --line:#d9d9d9;
  --white:#ffffff;
}
*{box-sizing:border-box;margin:0;padding:0}
html,body{width:1200px;height:5119px;overflow:hidden}
body{font-family:"Inter",sans-serif;color:var(--ink);background:var(--white);position:relative}
.abs{position:absolute}
h1,h2,h3,.display{font-family:"Plus Jakarta Sans",sans-serif}

/* Hero */
.hero{position:absolute;left:0;top:0;width:1200px;height:710px;
  background:linear-gradient(100deg,#5b564f 0%,#7b6f62 25%,#8a8378 50%,#9a958c 70%,#6f6a63 100%)}
.hero::after{content:"";position:absolute;inset:0;background:rgba(20,20,20,.45)}
.hero>*{z-index:1}
.nav{position:absolute;left:153px;top:28px;width:896px;height:62px;border:1.5px solid rgba(255,255,255,.55);
  border-radius:10px;background:rgba(255,255,255,.08);display:flex;align-items:center;padding:0 22px;z-index:2}
.brand{font-family:"Plus Jakarta Sans",sans-serif;font-weight:800;font-size:17px;color:var(--white);letter-spacing:-.3px}
.nav ul{margin-left:auto;display:flex;list-style:none;gap:6px;align-items:center}
.nav li{font-size:14px;color:var(--white);padding:6px 12px;border-radius:20px}
.nav li.active{background:var(--white);color:var(--ink);font-weight:500}
.hero-title{position:absolute;left:0;width:1200px;top:180px;text-align:center;color:var(--white);
  font-weight:800;font-size:41px;line-height:53px;letter-spacing:-1.6px;z-index:2}
.hero-title span{color:#33b87f}
.hero-sub{position:absolute;left:0;width:1200px;top:304px;text-align:center;color:var(--white);font-size:20px;line-height:32px;z-index:2}
.hero-btns{position:absolute;left:0;width:1200px;top:400px;display:flex;justify-content:center;gap:18px;z-index:2}
.btn{display:inline-flex;align-items:center;justify-content:center;background:var(--green);color:var(--white);
  font-family:"Plus Jakarta Sans",sans-serif;font-weight:700;font-size:14px;border-radius:26px;height:52px;padding:0 40px;letter-spacing:-.2px}
.rating-pill{position:absolute;left:478px;top:497px;width:286px;height:36px;border-radius:20px;background:rgba(60,60,60,.55);
  color:var(--white);font-size:12.5px;display:flex;align-items:center;justify-content:center;gap:10px;z-index:2}
.features{position:absolute;left:0;width:1200px;top:620px;display:flex;justify-content:center;z-index:2}
.feature{display:flex;flex-direction:column;align-items:center;gap:7px;color:rgba(255,255,255,.85);font-size:14px;padding:0 14px;position:relative}
.feature+.feature::before{content:"";position:absolute;left:0;top:34px;width:1px;height:20px;background:rgba(255,255,255,.6)}
.feature svg{width:26px;height:24px}

/* The House */
.photo{position:absolute;border-radius:14px}
.house-bedroom{left:99px;top:777px;width:447px;height:395px;background:linear-gradient(135deg,#b9b6ab,#8f8c80 55%,#5e6f66)}
.house-yard{left:0;top:1184px;width:252px;height:191px;border-radius:0 14px 14px 0;background:linear-gradient(160deg,#6f8a57,#8f7a5f 60%,#4f6640)}
.house-front{left:264px;top:1045px;width:320px;height:362px;background:linear-gradient(180deg,#4c8fd6 0%,#8ab8e0 35%,#6b8a55 60%,#3e5e33 100%);outline:12px solid var(--white)}
.section-title{font-weight:800;font-size:28px;letter-spacing:-.4px;color:var(--ink)}
.rule{height:2px;width:60px;background:var(--ink)}
.house-text{position:absolute;left:638px;top:772px;width:420px}
.house-text p{margin-top:34px;font-size:13px;line-height:20.6px;color:var(--text)}
.checks{list-style:none;margin-top:20px}
.checks li{display:flex;align-items:center;gap:10px;font-size:12.5px;color:var(--text);height:24.8px}
.checks svg{width:14px;height:14px;flex:none}
.btn-sm{height:36px;padding:0 22px;font-size:11px;border-radius:20px;margin-top:16px}

/* Gallery */
.centered{position:absolute;left:0;width:1200px;text-align:center}
.gal{top:1611px;height:408px;background:linear-gradient(160deg,#cfcdc6,#9d9b93 60%,#7a7a72)}
.dots{top:2068px;display:flex;justify-content:center;gap:8px}
.dots i{width:12px;height:12px;border-radius:50%;background:#d6d6d6;display:block}
.dots i.on{background:var(--green)}

/* Explore */
.card{position:absolute;width:216px;height:338px;border-radius:12px;background:var(--white);box-shadow:0 4px 14px rgba(0,0,0,.1);overflow:hidden}
.card .img{height:270px;border-radius:12px}
.card .label{height:68px;display:flex;align-items:center;justify-content:center;text-align:center;font-size:12.5px;font-weight:600;letter-spacing:.3px;color:var(--ink);line-height:16px}

/* Reviews */
.reviews{position:absolute;left:0;top:3062px;width:1200px;height:443px;background:var(--mint)}
.stars{display:flex;gap:3px}
.stars svg{width:15px;height:15px}
.rcard{position:absolute;top:143px;width:216px;height:246px;background:var(--white);border-radius:10px;box-shadow:0 3px 12px rgba(0,0,0,.07);padding:26px 24px}
.rcard p{margin-top:14px;font-size:12px;line-height:18px;color:var(--text);height:124px}
.reviewer{display:flex;align-items:center;gap:10px;margin-top:10px}
.avatar{width:34px;height:34px;border-radius:50%;background:linear-gradient(135deg,#b58b6b,#6d5443);flex:none}
.reviewer b{display:block;font-size:11px;font-weight:600;color:var(--ink)}
.reviewer span{font-size:10px;color:var(--muted)}
.arrow{position:absolute;top:200px;width:20px;height:40px}

/* FAQ */
.faq-img{left:153px;top:3720px;width:344px;height:365px;background:radial-gradient(circle at 55% 50%,#f0a04a 0%,#8b5a3a 18%,#6d6459 40%,#9c9488 100%)}
.faq-item{position:absolute;left:542px;width:507px;height:38px;border:1.5px solid #8f8f8f;border-radius:12px;display:flex;align-items:center;justify-content:space-between;padding:0 18px;font-size:13.5px;color:var(--ink)}
.faq-item svg{width:16px;height:16px}

/* CTA */
.cta{position:absolute;left:0;top:4159px;width:1200px;height:560px;background:linear-gradient(120deg,#3a3632,#5a534b 45%,#3d3934)}
.cta::after{content:"";position:absolute;inset:0;background:rgba(20,18,16,.35)}

/* Footer */
.footer{position:absolute;left:0;top:4640px;width:1200px;height:479px}
.footer-inner{color:var(--white)}
.f-head{font-family:"Plus Jakarta Sans",sans-serif;font-weight:800;font-size:13px;letter-spacing:-.2px}
.f-text{font-size:12.5px;line-height:19px}
.social{display:flex;gap:7px}
.social i{display:block;width:32px;height:32px;border-radius:50%;border:2.5px solid var(--white);background:var(--white)}
.map{left:773px;top:4773px;width:276px;height:228px;border-radius:10px;background:linear-gradient(135deg,#eef0ea,#e2e6dc 50%,#f2efe6)}
</style>
</head>
<body>

<svg width="0" height="0" style="position:absolute">
  <defs>
    <symbol id="star" viewBox="0 0 20 20"><path d="M10 1.5l2.6 5.6 6.1.7-4.5 4.2 1.2 6-5.4-3-5.4 3 1.2-6L1.3 7.8l6.1-.7z"/></symbol>
    <symbol id="tick" viewBox="0 0 16 16"><path d="M2 8.5l4 4L14 3.5" fill="none" stroke="currentColor" stroke-width="2.6" stroke-linecap="round" stroke-linejoin="round"/></symbol>
    <symbol id="plus" viewBox="0 0 16 16"><rect x="1.5" y="1.5" width="13" height="13" rx="3" fill="none" stroke="#555" stroke-width="1.3"/><path d="M8 5v6M5 8h6" stroke="#555" stroke-width="1.3"/></symbol>
  </defs>
</svg>

<!-- HERO -->
<header class="hero" role="img" aria-label="Living room with stone fireplace wall, wood stove and leather sofa">
  <nav class="nav">
    <div class="brand">BIRCH LANTERN RETREAT</div>
    <ul>
      <li class="active">Home</li><li>The House</li><li>Gallery</li><li>Explore Bend</li><li>Guest Reviews</li><li>FAQ</li><li>Contact</li>
    </ul>
  </nav>
  <h1 class="hero-title">YOUR BEND GETAWAY,<br>STEPS FROM THE <span>TANNERY ROW QUARTER</span></h1>
  <p class="hero-sub">A beautifully appointed 3-bedroom vacation home in<br>one of Bend's most convenient locations.</p>
  <div class="hero-btns"><span class="btn">BOOK DIRECT</span><span class="btn">CHECK AVAILABILITY</span></div>
  <div class="rating-pill"><svg width="15" height="15" fill="#fff"><use href="#star"/></svg>4.98 stars with 200+ guest reviews</div>
  <div class="features">
    <div class="feature"><svg viewBox="0 0 26 24" fill="none" stroke="#fff" stroke-width="1.6"><rect x="3" y="6" width="20" height="8" rx="2"/><path d="M2 14h22v5M2 14v5M6 10h5v-3M15 10h5v-3"/></svg>3 Bedrooms</div>
    <div class="feature"><svg viewBox="0 0 26 24" fill="none" stroke="#fff" stroke-width="1.6"><path d="M3 12h20v3a5 5 0 0 1-5 5H8a5 5 0 0 1-5-5zM7 12V5a2 2 0 0 1 4 0M8 20l-1 2M18 20l1 2"/></svg>2 Baths</div>
    <div class="feature"><svg viewBox="0 0 26 24" fill="none" stroke="#fff" stroke-width="1.6"><circle cx="9" cy="8" r="3.5"/><circle cx="18" cy="8" r="3"/><path d="M2 20a7 7 0 0 1 14 0M15 14a6 6 0 0 1 9 6"/></svg>Sleeps 6</div>
    <div class="feature"><svg viewBox="0 0 26 24" fill="none" stroke="#fff" stroke-width="1.6"><path d="M13 21S3 15 3 8.5A4.5 4.5 0 0 1 13 6a4.5 4.5 0 0 1 10 2.5C23 15 13 21 13 21z"/></svg>Pet Friendly</div>
    <div class="feature"><svg viewBox="0 0 26 24" fill="none" stroke="#fff" stroke-width="1.6"><circle cx="14" cy="4" r="2"/><path d="M13 8l-4 4 3 2v7M13 8l3 5 4 1M12 14l-4 7"/></svg>Walk to Tannery Row</div>
  </div>
</header>

<!-- THE HOUSE -->
<section class="house">
  <div class="photo house-bedroom" role="img" aria-label="Bedroom with chandelier, teal dresser and window"></div>
  <div class="photo house-yard" role="img" aria-label="Private fenced backyard with lawn and garden"></div>
  <div class="photo house-front" role="img" aria-label="Front of the house with porch, trees and blue sky"></div>
  <div class="house-text">
    <h2 class="section-title">THE HOUSE</h2>
    <div class="rule" style="margin-top:18px"></div>
    <p>Birch Lantern Retreat is designed to make your Bend stay feel easy, comfortable, and right at home. With three inviting bedrooms, two bathrooms, spacious living areas, and a well-equipped kitchen, there's room for everyone to relax after a day of exploring Central Oregon.</p>
    <ul class="checks" style="color:var(--green)">
      <li><svg><use href="#tick"/></svg>3 bedrooms</li>
      <li><svg><use href="#tick"/></svg>2 bathrooms</li>
      <li><svg><use href="#tick"/></svg>Sleeps up to 6 guests</li>
      <li><svg><use href="#tick"/></svg>Pet friendly</li>
      <li><svg><use href="#tick"/></svg>Approximately a 5-minute walk to Bend's Tannery Row Quarter</li>
      <li><svg><use href="#tick"/></svg>Near restaurants, shopping and Larkspur Fields Pavilion</li>
      <li><svg><use href="#tick"/></svg>Private fenced backyard</li>
      <li><svg><use href="#tick"/></svg>Covered outdoor area</li>
      <li><svg><use href="#tick"/></svg>Off-street driveway parking</li>
      <li><svg><use href="#tick"/></svg>Fireplace</li>
      <li><svg><use href="#tick"/></svg>Well-equipped kitchen</li>
      <li><svg><use href="#tick"/></svg>Staynest Prime Keeper</li>
      <li><svg><use href="#tick"/></svg>Staynest Visitor Pick</li>
      <li><svg><use href="#tick"/></svg>Top 1% of eligible Staynest homes</li>
      <li><svg><use href="#tick"/></svg>Approximately 4.98 stars with 200+ guest reviews</li>
    </ul>
    <span class="btn btn-sm">READ MORE</span>
  </div>
</section>

<!-- GALLERY -->
<h2 class="centered section-title" style="top:1494px">PHOTO GALLERY</h2>
<div class="abs rule" style="left:570px;top:1561px"></div>
<div class="photo gal" style="left:-14px;width:151px" role="img" aria-label="Bathroom with white vanity"></div>
<div class="photo gal" style="left:153px;width:435px" role="img" aria-label="Kitchen with dining table and white cabinets"></div>
<div class="photo gal" style="left:602px;width:435px" role="img" aria-label="Bedroom with chandelier and bright windows"></div>
<div class="photo gal" style="left:1053px;width:161px" role="img" aria-label="Bathroom with double vanity"></div>
<div class="centered dots"><i class="on"></i><i></i><i></i><i></i><i></i></div>

<!-- EXPLORE BEND -->
<h2 class="centered section-title" style="top:2152px">EXPLORE BEND</h2>
<div class="abs rule" style="left:570px;top:2216px"></div>
<div class="card" style="left:153px;top:2273px"><div class="img" role="img" aria-label="Waterfront district view" style="background:linear-gradient(180deg,#6fa6d8,#2f7bb8 45%,#e4e0d6)"></div><div class="label">TANNERY ROW QUARTER</div></div>
<div class="card" style="left:380px;top:2273px"><div class="img" role="img" aria-label="Riverside pavilion and lawn" style="background:linear-gradient(180deg,#3f86d6,#8bbbe4 35%,#4e7e3b 60%,#2e4f6a)"></div><div class="label">LARKSPUR FIELDS<br>PAVILION</div></div>
<div class="card" style="left:608px;top:2273px"><div class="img" role="img" aria-label="Deschutes River with pine forest" style="background:linear-gradient(180deg,#7eb3e0,#4b7a3e 45%,#5e8fa6 75%,#3c5e31)"></div><div class="label">DESCHUTES RIVER</div></div>
<div class="card" style="left:835px;top:2273px"><div class="img" role="img" aria-label="Restaurant interior with orange chairs" style="background:linear-gradient(180deg,#6c6258,#b7713a 60%,#4a3f37)"></div><div class="label">RESTAURANTS</div></div>
<div class="card" style="left:153px;top:2643px"><div class="img" role="img" aria-label="Brewery steel tanks" style="background:linear-gradient(160deg,#d4d4d2,#7c7c7c 55%,#3d3d3d)"></div><div class="label">BREWERIES</div></div>
<div class="card" style="left:380px;top:2643px"><div class="img" role="img" aria-label="Shopping at a clothing boutique" style="background:linear-gradient(160deg,#d9cfc2,#9e8b76 55%,#3d4a5a)"></div><div class="label">SHOPPING</div></div>
<div class="card" style="left:608px;top:2643px"><div class="img" role="img" aria-label="Aerial view of downtown Bend" style="background:linear-gradient(180deg,#8aa3b8,#5e6d58 35%,#7d6a52 70%,#4f5c3f)"></div><div class="label">DOWNTOWN BEND</div></div>
<div class="card" style="left:835px;top:2643px"><div class="img" role="img" aria-label="Outdoor landscape with windmill" style="background:linear-gradient(180deg,#5d96d6,#a9c8e6 45%,#6d8a4e 75%,#8a7a5c)"></div><div class="label">NEARBY OUTDOOR<br>RECREATION</div></div>

<!-- GUEST REVIEWS -->
<section class="reviews">
  <h2 class="abs section-title" style="left:153px;top:47px">GUEST REVIEWS</h2>
  <div class="abs rule" style="left:153px;top:98px;width:100px"></div>
  <div class="abs" style="left:922px;top:72px;display:flex;align-items:center;gap:6px;font-size:15px;font-weight:600">
    <div class="stars" style="fill:var(--green)"><svg><use href="#star"/></svg><svg><use href="#star"/></svg><svg><use href="#star"/></svg><svg><use href="#star"/></svg><svg><use href="#star"/></svg></div>4.98
  </div>
  <div class="abs" style="left:922px;top:98px;font-size:12px;color:var(--ink)">200+ Guest Reviews</div>

  <svg class="arrow" style="left:78px" viewBox="0 0 20 40" fill="none" stroke="#9a9a9a" stroke-width="2"><path d="M16 4L4 20l12 16"/></svg>
  <svg class="arrow" style="left:1098px" viewBox="0 0 20 40" fill="none" stroke="#9a9a9a" stroke-width="2"><path d="M4 4l12 16L4 36"/></svg>

  <div class="rcard" style="left:153px">
    <div class="stars" style="fill:var(--green)"><svg><use href="#star"/></svg><svg><use href="#star"/></svg><svg><use href="#star"/></svg><svg><use href="#star"/></svg><svg><use href="#star"/></svg></div>
    <p>Very cute place central to Tannery Row. The water fountain in the back was very peaceful and we enjoyed our stay. Thank you!</p>
    <div class="reviewer"><div class="avatar" role="img" aria-label="Guest profile photo"></div><div><b>Marisol</b><span>5 years on Staynest</span></div></div>
  </div>
  <div class="rcard" style="left:380px">
    <div class="stars" style="fill:var(--green)"><svg><use href="#star"/></svg><svg><use href="#star"/></svg><svg><use href="#star"/></svg><svg><use href="#star"/></svg><svg><use href="#star"/></svg></div>
    <p>This place is amazing and the personal touches were over the top! Wren was so kind and communicative. Great location, great house and we will definitely be back!</p>
    <div class="reviewer"><div class="avatar" role="img" aria-label="Guest profile photo" style="background:linear-gradient(135deg,#7fa0c4,#3f5f86)"></div><div><b>Greta</b><span>6 years on Staynest</span></div></div>
  </div>
  <div class="rcard" style="left:608px">
    <div class="stars" style="fill:var(--green)"><svg><use href="#star"/></svg><svg><use href="#star"/></svg><svg><use href="#star"/></svg><svg><use href="#star"/></svg><svg><use href="#star"/></svg></div>
    <p>Perfect location! Everything was only a 7 min drive away. We were able to walk to the pavilion for a show, it was great! Would stay again for sure!</p>
    <div class="reviewer"><div class="avatar" role="img" aria-label="Guest profile photo" style="background:linear-gradient(135deg,#9aa68a,#4f5a45)"></div><div><b>Tessa</b><span>Portland, Oregon</span></div></div>
  </div>
  <div class="rcard" style="left:835px">
    <div class="stars" style="fill:var(--green)"><svg><use href="#star"/></svg><svg><use href="#star"/></svg><svg><use href="#star"/></svg><svg><use href="#star"/></svg><svg><use href="#star"/></svg></div>
    <p>Space was exactly what we were looking for. Close to Tannery Row and River path. Appreciate that it was pet friendly.</p>
    <div class="reviewer"><div class="avatar" role="img" aria-label="Guest profile photo" style="background:linear-gradient(135deg,#a8806a,#5b4030)"></div><div><b>Noreen</b><span>Eugene, Oregon</span></div></div>
  </div>
</section>

<!-- FAQ -->
<h2 class="abs section-title" style="left:153px;top:3568px;line-height:41px">FREQUENTLY<br>ASKED QUESTIONS</h2>
<div class="abs rule" style="left:153px;top:3674px;width:100px"></div>
<div class="photo faq-img" role="img" aria-label="Backyard patio with fire table"></div>
<div class="faq-item" style="top:3569px">Is Birch Lantern Retreat pet friendly?<svg><use href="#plus"/></svg></div>
<div class="faq-item" style="top:3621px">How many guests can stay at the house?<svg><use href="#plus"/></svg></div>
<div class="faq-item" style="top:3674px">Is parking available?<svg><use href="#plus"/></svg></div>
<div class="faq-item" style="top:3726px">How close is the Tannery Row Quarter?<svg><use href="#plus"/></svg></div>
<div class="faq-item" style="top:3779px">What time is check-in and check-out?<svg><use href="#plus"/></svg></div>
<div class="faq-item" style="top:3831px">How does check-in work?<svg><use href="#plus"/></svg></div>
<div class="faq-item" style="top:3884px">What is the cancellation policy?<svg><use href="#plus"/></svg></div>
<div class="faq-item" style="top:3936px">Are there additional fees or taxes?<svg><use href="#plus"/></svg></div>
<div class="faq-item" style="top:3989px">Can I book directly?<svg><use href="#plus"/></svg></div>
<div class="faq-item" style="top:4041px">Is the property suitable for families?<svg><use href="#plus"/></svg></div>

<!-- CTA -->
<section class="cta" role="img" aria-label="Dim bedroom with chandelier and lamp"></section>
<h2 class="centered display" style="top:4278px;color:var(--white);font-weight:800;font-size:46px;letter-spacing:-.5px;z-index:2">HAVE A QUESTION?</h2>
<p class="centered" style="top:4356px;color:var(--white);font-size:23px;z-index:2">Get in touch with us and we'll be happy to help.</p>
<div class="centered" style="top:4419px;display:flex;justify-content:center;gap:20px;z-index:2"><span class="btn" style="height:50px;padding:0 30px;font-size:15px">CONTACT US</span><span class="btn" style="height:50px;padding:0 42px;font-size:15px">BOOK DIRECT</span></div>

<!-- FOOTER -->
<footer class="footer">
  <svg class="abs" style="left:0;top:0" width="1200" height="479" viewBox="0 0 1200 479">
    <path d="M0 40 C150 70 300 20 450 45 C600 70 750 35 900 50 C1050 65 1130 30 1200 40 L1200 479 L0 479Z" fill="var(--footer)"/>
    <path d="M0 32 C170 62 320 14 470 38 C620 62 760 28 920 42 C1060 56 1140 22 1200 30" fill="none" stroke="#7fd4b0" stroke-width="3"/>
    <line x1="153" y1="367" x2="725" y2="367" stroke="rgba(255,255,255,.5)" stroke-width="1"/>
  </svg>
</footer>
<div class="footer-inner">
  <div class="abs display" style="left:151px;top:4772px;font-weight:800;font-size:22px;letter-spacing:-.6px;color:var(--white);width:250px;line-height:26px">BIRCH LANTERN RETREAT</div>
  <div class="abs f-head" style="left:153px;top:4856px;font-size:10.5px;color:var(--white)">FOLLOW US</div>
  <div class="abs social" style="left:153px;top:4883px" aria-label="Social media links"><i></i><i></i><i></i><i></i><i></i></div>

  <div class="abs f-head" style="left:417px;top:4772px;color:var(--white)">CONTACT US</div>
  <svg class="abs" style="left:414px;top:4820px" width="14" height="16" viewBox="0 0 14 16" fill="#fff"><path d="M7 0a5.5 5.5 0 0 0-5.5 5.5C1.5 10 7 16 7 16s5.5-6 5.5-10.5A5.5 5.5 0 0 0 7 0zm0 7.6a2.1 2.1 0 1 1 0-4.2 2.1 2.1 0 0 1 0 4.2z"/></svg>
  <div class="abs f-text" style="left:446px;top:4812px;color:var(--white)">418 Quarry Lane<br>Bend, OR 97702<br>United States</div>
  <svg class="abs" style="left:414px;top:4876px" width="14" height="14" viewBox="0 0 24 24" fill="#fff"><path d="M6.6 10.8a15 15 0 0 0 6.6 6.6l2.2-2.2a1 1 0 0 1 1-.25 11.4 11.4 0 0 0 3.6.57 1 1 0 0 1 1 1V20a1 1 0 0 1-1 1A17 17 0 0 1 3 4a1 1 0 0 1 1-1h3.5a1 1 0 0 1 1 1c0 1.25.2 2.45.57 3.57a1 1 0 0 1-.25 1z"/></svg>
  <div class="abs f-text" style="left:446px;top:4874px;color:var(--white)">(541) 555-0148</div>
  <svg class="abs" style="left:414px;top:4906px" width="14" height="12" viewBox="0 0 14 12" fill="#fff"><path d="M0 1h14v10H0z"/><path d="M0 1l7 5 7-5" fill="none" stroke="var(--footer)" stroke-width="1.4"/></svg>
  <div class="abs f-text" style="left:446px;top:4902px;color:var(--white)">stay@birchlantern-example.net</div>

  <div class="abs f-head" style="left:638px;top:4772px;color:var(--white)">MENU</div>
  <div class="abs f-text" style="left:638px;top:4808px;color:var(--white);line-height:22.6px">Home<br>The House<br>Gallery<br>Explore Bend<br>Guest Reviews<br>FAQ<br>Contact</div>

  <div class="photo map" role="img" aria-label="Map showing the property location in Bend, Oregon"></div>
  <svg class="abs" style="left:900px;top:4868px" width="26" height="32" viewBox="0 0 26 32"><path d="M13 0a12 12 0 0 0-12 12c0 9 12 20 12 20s12-11 12-20A12 12 0 0 0 13 0z" fill="#d81f4a"/><circle cx="13" cy="12" r="4.5" fill="#fff"/></svg>

  <div class="centered" style="top:5050px;font-size:12px;color:var(--white)">Copyright © 2026 All Rights Reserved</div>
</div>

</body>
</html>
```